Business Card Design Project : Ridgeline Press

In preparation for market launch, Tamarind's Ridgeline Press require the development of a business card. Ridgeline Press is a Community online publishing web portal. We provide the the city of Whistler located in B.C. (Canada) business directories, News, Classified ads, News, Events and blogs etc.

The main focus of the brand is to help local businesses to corporate with their online advertisement and marketing. Meeting our clients face to face is a must (B2B).

Target Market(s)

The target market is B2B customers. Business Owners to Marketing, advertising Managers

Industry/Entity Type

Business

Requirements
Must have
• - The business card will be two sided.
the BACK side will have our logo which consist of (icon, url,slogan) submited. The logo will be middle and centred.

The FRONT side should have company details:

Company Legal Name: TAMARIND RIDGELINE MEDIA

Owen Farsk
Director of Sales & Marketing

www.tamarindridgeline.biz
owen@tamarindridgeline.biz

Phone: 604 317 8842
#2714 - 582 E. Halvern St.
Vancouver, B.C. V7K2R4 Canada
Nice to have
• - For the "FRONT" side of our business card. You can separate or re-arrange with our logo components (icon, logo,slogan). It does not have to be together.

Also our company legal name is rather long so arrange or organize the name in a way to make it shorter. Your experience and creativity will have to come in play.
Should not have
• should not have other colors beside logo color and black text (2 colors). Also nothing Three dimensional

```html
<!DOCTYPE html>
<html lang="en">
<head>
<meta charset="utf-8">
<title>Ridgeline Press – Business Card</title>
<link href="https://fonts.googleapis.com/css2?family=Arimo:wght@400;700&family=Open+Sans:wght@400;600;700&display=swap" rel="stylesheet">
<style>
  :root {
    --brand-blue: #2a7cc4;
    --ink: #111111;
    --paper: #ffffff;
    --pattern-tint: #eef0f8;
    --backdrop: #4a4a4a;
    --white: #ffffff;
  }
  * { margin: 0; padding: 0; box-sizing: border-box; }
  html, body { width: 1200px; height: 900px; overflow: hidden; }
  body { background: var(--backdrop); position: relative; font-family: "Arimo", Arial, sans-serif; }

  .card {
    position: absolute;
    top: 300px;
    width: 525px;
    height: 300px;
    background: var(--paper);
    overflow: hidden;
  }
  .card--back { left: 58px; }
  .card--front { left: 617px; }

  .card__pattern {
    position: absolute;
    inset: 0;
    background: linear-gradient(180deg, var(--pattern-tint), var(--paper) 50%, var(--pattern-tint));
  }

  /* Back side */
  .brand-name {
    position: absolute;
    left: 0; right: 0;
    text-align: center;
    font-family: "Open Sans", Arial, sans-serif;
    font-weight: 700;
    color: var(--brand-blue);
  }
  .card--back .brand-name { top: 92px; font-size: 40px; }
  .web-address {
    position: absolute;
    font-family: "Open Sans", Arial, sans-serif;
    font-weight: 700;
    color: var(--ink);
    font-size: 23px;
    letter-spacing: -0.3px;
  }
  .slogan {
    position: absolute;
    font-family: "Open Sans", Arial, sans-serif;
    color: var(--brand-blue);
    font-size: 17px;
  }
  .card--back .web-address { left: 0; right: 0; text-align: center; top: 162px; }
  .card--back .slogan { left: 0; right: 0; text-align: center; padding-left: 30px; top: 190px; }
  .band-blue { position: absolute; background: var(--brand-blue); }
  .band-black { position: absolute; background: var(--ink); }
  .card--back .band-blue { left: 0; right: 0; top: 258px; height: 25px; }
  .card--back .band-black { left: 0; right: 0; top: 283px; height: 17px; }

  /* Front side */
  .company-name {
    position: absolute;
    left: 38px; top: 43px;
    font-weight: 700;
    font-size: 21px;
    color: var(--ink);
  }
  .card--front .band-blue {
    left: 0; top: 80px; width: 250px; height: 117px;
    border-top-right-radius: 0;
  }
  .card--front .band-black { left: 0; top: 197px; width: 250px; height: 15px; }
  .contact {
    position: absolute;
    left: 38px; top: 86px;
    color: var(--ink);
  }
  .contact__name { font-weight: 700; font-size: 15px; line-height: 16px; }
  .contact__role { font-size: 13px; line-height: 16px; }
  .contact__line { font-size: 13px; line-height: 17px; display: flex; align-items: center; gap: 6px; }
  .contact__lines { margin-top: 6px; }
  .contact__address { margin-top: 5px; font-size: 12px; line-height: 15px; }
  .icon { width: 11px; height: 11px; fill: var(--ink); flex: none; }

  .card--front .brand-name { left: 250px; right: 0; top: 112px; font-size: 28px; }
  .card--front .web-address { right: 28px; top: 232px; font-size: 22px; }
  .card--front .slogan { right: 60px; top: 257px; font-size: 16px; }
</style>
</head>
<body>

  <section class="card card--back" aria-label="Business card back">
    <div class="card__pattern" role="img" aria-label="Faint repeating brand pattern"></div>
    <div class="brand-name">Ridgeline Press</div>
    <div class="web-address">www.tamarindridgeline.biz</div>
    <div class="slogan">Your information gateway</div>
    <div class="band-blue"></div>
    <div class="band-black"></div>
  </section>

  <section class="card card--front" aria-label="Business card front">
    <div class="card__pattern" role="img" aria-label="Faint repeating brand pattern"></div>
    <div class="company-name">Tamarind Ridgeline Media</div>
    <div class="band-blue"></div>
    <div class="band-black"></div>
    <div class="contact">
      <div class="contact__name">OWEN FARSK</div>
      <div class="contact__role">Director of Sales &amp; Marketing</div>
      <div class="contact__lines">
        <div class="contact__line">
          <svg class="icon" viewBox="0 0 12 12" aria-hidden="true"><path d="M3 0h6a1 1 0 0 1 1 1v10a1 1 0 0 1-1 1H3a1 1 0 0 1-1-1V1a1 1 0 0 1 1-1zm0 1.5v7.5h6V1.5zM5 10h2v1H5z"/></svg>
          <span>604 317 8842</span>
        </div>
        <div class="contact__line">
          <svg class="icon" viewBox="0 0 12 12" aria-hidden="true"><path d="M0 2h12v8H0zm1 1v.4l5 3.2 5-3.2V3zm0 1.6V9h10V4.6L6 7.8z"/></svg>
          <span>owen@tamarindridgeline.biz</span>
        </div>
      </div>
      <div class="contact__address">#2714 - 582 E. Halvern St.<br>Vancouver, B.C. V7K2R4 Canada</div>
    </div>
    <div class="brand-name">Ridgeline Press</div>
    <div class="web-address">www.tamarindridgeline.biz</div>
    <div class="slogan">Your information gateway</div>
  </section>

</body>
</html>
```